Tamsorellium we are a young innovative brand about making life easier for people with a disability

Our tag line is Making Life Easy, we are still a relatively new company trying to bring innovation and excitement into the disability space - with latest products and technology - we do have existing website but need to unpgrade for a stronger visual presence.

```html
<!DOCTYPE html>
<html lang="en">
<head>
<meta charset="utf-8">
<title>Tamsorellium – Making Life Easier</title>
<link href="https://fonts.googleapis.com/css2?family=Arimo:wght@400&family=Chakra+Petch:ital,wght@1,700&family=Poppins:wght@400;500;600;700&display=swap" rel="stylesheet">
<style>
:root{
  --red:#e30613;
  --black:#000;
  --ink:#1a1a1a;
  --grey:#6b6b6b;
  --light:#f2f2f2;
  --pink:#fbeaea;
  --white:#fff;
}
*{margin:0;padding:0;box-sizing:border-box}
html,body{width:1200px;height:3809px;overflow:hidden}
body{position:relative;background:var(--white);font-family:"Poppins",sans-serif;color:var(--ink)}
.abs{position:absolute}
.display{font-family:"Chakra Petch",sans-serif;font-style:italic;font-weight:700;text-transform:uppercase;letter-spacing:1px}
.brand{display:flex;align-items:center;gap:12px}
.brand-dot{width:62px;height:62px;border-radius:50%;background:var(--red)}
.brand-name{font-family:"Poppins",sans-serif;font-weight:700;font-size:26px;color:var(--red)}
.search{left:584px;top:25px;width:377px;height:42px;border:1px solid #333;padding:0 14px;font-size:13px;color:#999;line-height:40px}
.cart{left:969px;top:25px;width:119px;height:42px;background:var(--red);color:#fff;font-size:16px;display:flex;align-items:center;justify-content:center;gap:10px}
.nav{left:0;top:90px;width:1200px;height:56px;background:var(--red);border-bottom:4px solid #222;display:flex;padding-left:192px}
.nav span{color:#fff;font-size:15px;line-height:52px;padding:0 14px}
.nav .active{background:var(--black)}
.hero{left:0;top:148px;width:1200px;height:451px;background:linear-gradient(90deg,#eeeeec 0%,#e4e0da 40%,#c9b7a3 62%,#a59a90 80%,#8f8a86 100%)}
.hero h1{position:absolute;left:115px;top:100px;font-size:38px;line-height:60px;color:var(--ink)}
.hero p{position:absolute;left:115px;top:218px;width:525px;font-family:"Arimo",sans-serif;font-size:14.5px;line-height:30px;color:#333}
.sec-title{font-size:36px;color:var(--ink)}
.body-copy{font-family:"Arimo",sans-serif;font-size:14.5px;line-height:30px;color:var(--grey)}
.btn{background:var(--red);color:#fff;font-size:17px;display:flex;align-items:center;justify-content:center}
.shop{left:0;top:1278px;width:1200px;height:491px;background:var(--light)}
.card{position:absolute;top:192px;width:226px;height:203px;border:1px solid #333;background:var(--light)}
.card .ico{position:absolute;left:70px;top:40px;width:90px;height:70px}
.card .lbl{position:absolute;left:0;right:0;top:140px;text-align:center;color:var(--red);font-size:16.5px}
.arrows{display:flex;gap:16px}
.side-list li{list-style:none;color:#fff;font-size:24px;line-height:30px}
.pcard{position:absolute;top:1998px;width:258px;height:412px;background:#fff}
.field{position:absolute;background:#fff;font-size:13px;color:#555;padding:0 24px;line-height:50px;box-shadow:0 1px 3px rgba(0,0,0,.06)}
.footer{left:0;top:3343px;width:1200px;height:466px;background:var(--black);color:#fff}
.foot-head{color:var(--red);font-size:14px}
.foot-links{list-style:none;font-size:13.5px;line-height:26px;color:#ddd}
.pay{width:48px;height:25px;border-radius:3px}
</style>
</head>
<body>

<!-- Header -->
<div class="abs brand" style="left:110px;top:15px"><div class="brand-dot"></div><span class="brand-name">Tamsorellium</span></div>
<div class="abs search">Search all products....</div>
<div class="abs cart display">Cart
  <svg width="22" height="18" viewBox="0 0 22 18"><path d="M1 2h4l3 10h10l3-8H7" fill="none" stroke="#fff" stroke-width="2.2"/><circle cx="9" cy="16" r="1.6" fill="#fff"/><circle cx="17" cy="16" r="1.6" fill="#fff"/></svg>
</div>
<nav class="abs nav display">
  <span class="active">Wheelchairs</span><span>Parts</span><span>Accessories</span><span>Bargain Center</span><span>Online Invoice/Quotes</span><span>Scooters</span>
</nav>

<!-- Hero -->
<section class="abs hero" role="img" aria-label="Woman in a manual wheelchair at a city bus stop">
  <h1 class="display">Welcome to Tamsorellium<br>Making Life Easier</h1>
  <p>Are you trying to find the ideal wheelchair? Due to the vast number of possibilities, selecting a simple mobility item like a wheelchair can easily become overwhelming.</p>
</section>

<!-- Wheelchairs for sale -->
<div class="abs" role="img" aria-label="Woman in a teal top seated in a red and black active wheelchair" style="left:140px;top:718px;width:370px;height:450px;background:linear-gradient(180deg,#f6f6f6 0%,#e8ece9 35%,#ead7d4 70%,#f6f6f6 100%)"></div>
<h2 class="abs display sec-title" style="left:600px;top:702px">Wheelchairs for Sale</h2>
<div class="abs body-copy" style="left:603px;top:785px;width:480px">
  <p>Are you trying to find the ideal wheelchair? Due to the vast number of possibilities, selecting a simple mobility item like a wheelchair can easily become overwhelming.</p>
  <p style="margin-top:30px">Tamsorellium offers wheelchairs for sale in various sizes, styles, price ranges, and combinations that meet a range of demands and requirements you need.</p>
  <p style="margin-top:30px">Everyone may find wheelchairs at Tamsorellium. We offer manual, power-assist units, and wheelchair accessories for sale and rental.</p>
</div>
<div class="abs btn display" style="left:601px;top:1120px;width:145px;height:48px">Read More</div>

<!-- Shop for -->
<section class="abs shop">
  <h2 class="abs display sec-title" style="left:0;right:0;top:88px;text-align:center">Shop For</h2>
  <div class="card" style="left:117px"><svg class="ico" viewBox="0 0 90 70"><circle cx="55" cy="35" r="35" fill="#f6dcdc"/><rect x="10" y="22" width="50" height="34" rx="6" fill="none" stroke="#333" stroke-width="2.5"/><rect x="25" y="14" width="20" height="8" fill="none" stroke="#333" stroke-width="2.5"/></svg><div class="lbl display">Accessories</div></div>
  <div class="card" style="left:360px"><svg class="ico" viewBox="0 0 90 70"><circle cx="55" cy="35" r="35" fill="#f6dcdc"/><circle cx="35" cy="48" r="14" fill="none" stroke="#333" stroke-width="2.5"/><path d="M28 14v24h24l6 14" fill="none" stroke="#333" stroke-width="2.5"/></svg><div class="lbl display">Active Wheelchairs</div></div>
  <div class="card" style="left:603px"><svg class="ico" viewBox="0 0 90 70"><circle cx="55" cy="35" r="35" fill="#f6dcdc"/><path d="M20 16h44M34 16v38h14" fill="none" stroke="#333" stroke-width="2.5"/></svg><div class="lbl display">Armrests</div></div>
  <div class="card" style="left:847px"><svg class="ico" viewBox="0 0 90 70"><circle cx="55" cy="35" r="35" fill="#f6dcdc"/><path d="M40 14v42M26 20h28M26 50h28" fill="none" stroke="#333" stroke-width="2.5"/><rect x="20" y="14" width="8" height="12" fill="none" stroke="#333" stroke-width="2"/><rect x="52" y="14" width="8" height="12" fill="none" stroke="#333" stroke-width="2"/><rect x="20" y="44" width="8" height="12" fill="none" stroke="#333" stroke-width="2"/><rect x="52" y="44" width="8" height="12" fill="none" stroke="#333" stroke-width="2"/></svg><div class="lbl display">Axles, Hubs &amp; Parts</div></div>
  <div class="abs arrows" style="left:576px;top:442px">
    <svg width="16" height="14" viewBox="0 0 16 14"><path d="M15 7H2M7 1L1 7l6 6" fill="none" stroke="#222" stroke-width="1.8"/></svg>
    <svg width="16" height="14" viewBox="0 0 16 14"><path d="M1 7h13M9 1l6 6-6 6" fill="none" stroke="#222" stroke-width="1.8"/></svg>
  </div>
</section>

<!-- Power assist units -->
<div class="abs" role="img" aria-label="Close-up of a hand on a wheelchair wheel" style="left:0;top:1769px;width:507px;height:778px;background:linear-gradient(160deg,#2c3a44 0%,#4a5258 30%,#6a4a44 48%,#4a4f52 70%,#6b6a66 100%)"></div>
<div class="abs btn display" style="left:111px;top:1997px;width:305px;height:52px;font-size:24px">Power Assist Units</div>
<ul class="abs side-list display" style="left:111px;top:2090px">
  <li>Bags</li>
  <li style="margin-top:35px">Brakes/Locks &amp;<br>Components</li>
  <li style="margin-top:35px">Movaline</li>
</ul>
<h2 class="abs display sec-title" style="left:535px;top:1860px">Power Assist Units</h2>
<a class="abs" style="left:535px;top:1920px;font-size:16px;color:var(--red);text-decoration:underline">More power assist units</a>

<div class="pcard" style="left:430px;background:#fbf1f1">
  <div class="abs" style="left:14px;top:8px;font-size:30px;line-height:37px;font-weight:500;color:#222">Torvane<br>Mini</div>
  <div class="abs" style="left:190px;top:14px;width:46px;height:56px;border:2px solid #333;border-radius:4px 4px 20px 20px"></div>
  <div class="abs" role="img" aria-label="Wheelchair with a compact power assist attachment" style="left:20px;top:110px;width:220px;height:90px;background:linear-gradient(180deg,#fbf1f1 0%,#cfc9c6 60%,#9a9492 100%)"></div>
  <div class="abs display" style="left:20px;top:238px;color:var(--red);font-size:14px">Torvane Mini by Torvacare</div>
  <div class="abs" style="left:20px;top:264px;width:225px;font-size:14.5px;line-height:24px;color:#333">is a revolutionary wheelchair device, being your personal UNiversal Assistant and guide</div>
  <div class="abs display" style="left:20px;top:360px;color:var(--red);font-size:17px">$4,850</div>
  <svg class="abs" style="left:106px;top:362px" width="18" height="16" viewBox="0 0 22 18"><path d="M1 2h4l3 10h10l3-8H7" fill="#222" stroke="#222" stroke-width="2"/><circle cx="9" cy="16" r="1.6" fill="#222"/><circle cx="17" cy="16" r="1.6" fill="#222"/></svg>
</div>
<div class="pcard" style="left:704px"><div class="abs" role="img" aria-label="Red and black handbike power attachment" style="left:14px;top:110px;width:230px;height:230px;background:linear-gradient(135deg,#ffffff 0%,#e9d5d5 30%,#c8868a 50%,#e9d5d5 70%,#ffffff 100%)"></div></div>
<div class="pcard" style="left:976px;width:240px"><div class="abs" role="img" aria-label="Black electric wheelchair drive unit" style="left:40px;top:60px;width:160px;height:300px;background:linear-gradient(90deg,#ffffff 0%,#cfcfcf 30%,#8a8a8a 50%,#cfcfcf 70%,#ffffff 100%)"></div></div>
<div class="abs arrows" style="left:1057px;top:2496px">
  <svg width="16" height="14" viewBox="0 0 16 14"><path d="M15 7H2M7 1L1 7l6 6" fill="none" stroke="#222" stroke-width="1.8"/></svg>
  <svg width="16" height="14" viewBox="0 0 16 14"><path d="M1 7h13M9 1l6 6-6 6" fill="none" stroke="#222" stroke-width="1.8"/></svg>
</div>

<!-- Contact -->
<div class="abs" style="left:0;top:2547px;width:1200px;height:796px;background:var(--light)"></div>
<h2 class="abs display sec-title" style="left:110px;top:2645px">Contact Us</h2>
<p class="abs" style="left:112px;top:2712px;font-size:16px;color:var(--red)">We'll get back to you as soon as we can</p>
<div class="field" style="left:113px;top:2789px;width:265px">First Name</div>
<div class="field" style="left:401px;top:2789px;width:265px">Last Name</div>
<div class="field" style="left:113px;top:2870px;width:265px">Email Address</div>
<div class="field" style="left:401px;top:2870px;width:265px">Phone Number</div>
<div class="field" style="left:113px;top:2951px;width:553px;height:200px;padding-top:12px;line-height:26px">Message</div>
<div class="abs btn display" style="left:112px;top:3182px;width:145px;height:46px">Submit</div>
<div class="abs" style="left:772px;top:2660px;width:308px;height:323px;background:linear-gradient(180deg,#3e4a3a 0%,#2b2e30 60%,#222 100%)" role="img" aria-label="Man in a wheelchair outdoors"></div>
<div class="abs" style="left:928px;top:2835px;width:140px;height:140px;background:var(--red)"></div>
<div class="abs" style="left:712px;top:2870px;width:328px;height:358px;background:linear-gradient(160deg,#8aa06a 0%,#6d7a55 40%,#b7a58c 75%,#5c6f8a 100%)" role="img" aria-label="Young man kneeling beside an elderly woman in a wheelchair in a park"></div>

<!-- Footer -->
<footer class="abs footer">
  <div class="abs brand" style="left:160px;top:130px"><div class="brand-dot" style="width:56px;height:56px"></div><span class="brand-name">Tamsorellium</span></div>
  <div class="abs display foot-head" style="left:155px;top:225px">Subscribe to our newsletter</div>
  <div class="abs" style="left:155px;top:272px;width:259px;height:45px;background:#fff;color:#555;font-size:14px;line-height:45px;padding-left:28px">Email Address</div>
  <div class="abs" style="left:414px;top:272px;width:177px;height:45px;background:var(--red);color:#fff;font-size:16px;font-weight:500;line-height:45px;text-align:center">Subscribe Here</div>
  <div class="abs" style="left:653px;top:108px;width:1px;height:210px;background:#666"></div>
  <div class="abs" style="left:903px;top:108px;width:1px;height:210px;background:#666"></div>
  <div class="abs display foot-head" style="left:706px;top:110px">Quick Links</div>
  <ul class="abs foot-links" style="left:704px;top:143px"><li>Search</li><li>About us</li><li>Privacy Policy</li><li>Postage</li><li>International Shipping</li><li>Terms of Service</li><li>Returns Policy</li></ul>
  <div class="abs display foot-head" style="left:943px;top:110px">Get in Touch</div>
  <ul class="abs foot-links" style="left:940px;top:143px"><li>Contact Us</li><li>Shipping</li><li>Contact Details</li></ul>
  <div class="abs" style="left:0;right:0;top:362px;display:flex;justify-content:center;gap:26px;font-size:13.5px;color:#ddd"><span>Wheelchairs</span><span>Parts</span><span>Accessories</span><span>Bargain Center</span><span>Online Invoice/Quotes</span><span>Scooters</span></div>
  <div class="abs" style="left:108px;top:400px;width:976px;height:1px;background:#555"></div>
  <div class="abs" style="left:110px;top:420px;font-size:12px">© 2023 Tamsorellium</div>
  <div class="abs" style="left:762px;top:415px;display:flex;gap:11px">
    <div class="pay" style="background:#fff"></div><div class="pay" style="background:#fff"></div><div class="pay" style="background:#fff"></div><div class="pay" style="background:#fff"></div>
  </div>
  <div class="abs" style="left:1010px;top:418px;width:20px;height:20px;background:#fff"></div>
  <div class="abs" style="left:1062px;top:420px;font-size:12px">C64</div>
</footer>

</body>
</html>
```